Granite Hollow Roofing & Exteriors Ltd

I would like to start a Facebook page for business that outlines granite hollow roofing . We have been in business since 2005 & have completed more than 5000 projects . Our company is area licensed, insured , covered by qlr , mzc member , journey man roofers , offer financing, zero down payment required , free quotes , serving red deer & area .

Please do not put years on the homepage.

Target Market(s)

Roofers in red deer & central Alberta

Industry/Entity Type

Roofing

Requirements
Must have
• Shingles , soffit , fascia , siding , gutters , roof repair , exterior painting , exterior washing .

```html
<!DOCTYPE html>
<html lang="en">
<head>
<meta charset="UTF-8">
<title>Granite Hollow Roofing & Exteriors – Cover</title>
<link rel="stylesheet" href="https://fonts.googleapis.com/css2?family=Poppins:wght@400;500;700&display=swap">
<style>
  :root {
    --brand-red: #b5202c;
    --brand-navy: #2e3b4c;
    --paper: #f3efed;
    --paper-warm: #e9dfda;
    --white: #ffffff;
    --badge-navy: #1f4f86;
    --badge-blue: #1d5c8c;
    --ink: #1c1c1c;
  }
  * { margin: 0; padding: 0; box-sizing: border-box; }
  html, body { width: 1200px; height: 457px; overflow: hidden; }
  body { font-family: "Poppins", sans-serif; background: var(--paper); }

  .cover {
    position: relative;
    width: 1200px;
    height: 457px;
    overflow: hidden;
    background:
      radial-gradient(ellipse 340px 220px at 180px 120px, var(--paper-warm), transparent 70%),
      radial-gradient(ellipse 300px 200px at 560px 60px, #ece3df, transparent 70%),
      linear-gradient(90deg, #f1ebe8 0%, #f5f2f1 60%, #f7f6f6 100%);
  }

  .brand {
    position: absolute;
    left: 70px;
    top: 38px;
    display: flex;
    align-items: flex-start;
    gap: 8px;
  }
  .brand-mark {
    width: 11px;
    height: 11px;
    margin-top: 3px;
    background: var(--brand-red);
  }
  .brand-name {
    color: var(--brand-navy);
    font-weight: 500;
    font-size: 14px;
    line-height: 16px;
    letter-spacing: 0.2px;
    white-space: nowrap;
  }

  .headline {
    position: absolute;
    left: 89px;
    top: 104px;
    color: var(--brand-red);
    white-space: nowrap;
  }
  .headline-lead {
    font-size: 22px;
    font-weight: 500;
    line-height: 22px;
    letter-spacing: 0.3px;
  }
  .headline-main {
    margin-top: 2px;
    font-size: 44px;
    font-weight: 700;
    line-height: 36px;
    letter-spacing: -0.3px;
  }

  .services {
    position: absolute;
    left: 89px;
    top: 279px;
    display: flex;
    gap: 13px;
  }
  .services-label {
    background: var(--brand-red);
    color: var(--white);
    font-size: 12px;
    font-weight: 500;
    letter-spacing: 0.8px;
    width: 98px;
    height: 18px;
    display: flex;
    align-items: center;
    justify-content: center;
    flex-shrink: 0;
  }
  .services-list {
    color: var(--ink);
    font-size: 17px;
    font-weight: 500;
    line-height: 22px;
    margin-top: -2px;
    white-space: nowrap;
  }

  .accreditations {
    position: absolute;
    left: 201px;
    top: 358px;
    display: flex;
    align-items: center;
    gap: 30px;
  }
  .badge-plain {
    width: 120px;
    height: 24px;
    border: 2px solid var(--badge-navy);
    border-radius: 4px;
  }
  .badge-solid {
    width: 75px;
    height: 28px;
    background: var(--badge-blue);
    border-radius: 4px;
  }

  .contact-bar {
    position: absolute;
    left: 0;
    top: 397px;
    width: 540px;
    height: 45px;
    background: var(--brand-red);
    clip-path: polygon(0 0, 100% 0, 95% 100%, 0 100%);
    display: flex;
    align-items: center;
    padding-left: 89px;
    gap: 24px;
    color: var(--white);
    font-size: 15px;
    font-weight: 500;
    letter-spacing: 0.3px;
    white-space: nowrap;
  }
  .contact-phone { font-size: 16px; }

  .collage {
    position: absolute;
    right: 0;
    top: 0;
    width: 720px;
    height: 457px;
  }
</style>
</head>
<body>
<main class="cover">

  <header class="brand">
    <span class="brand-mark"></span>
    <div class="brand-name">GRANITE HOLLOW<br>ROOFING<br>&amp; EXTERIORS</div>
  </header>

  <section class="headline">
    <p class="headline-lead">WE SPECIALIZE IN</p>
    <h1 class="headline-main">RESIDENTIAL,<br>COMMERCIAL AND<br>INDUSTRIAL ROOFING</h1>
  </section>

  <section class="services">
    <div class="services-label">SERVICES:</div>
    <p class="services-list">SHINGLES, SOFFIT, FASCIA, SIDING,<br>GUTTERS, ROOF REPAIR, EXTERIOR PAINTING,<br>EXTERIOR WASHING AND MORE...</p>
  </section>

  <section class="accreditations">
    <div class="badge-plain" role="img" aria-label="QLR coverage badge"></div>
    <div class="badge-solid" role="img" aria-label="MZC member badge"></div>
  </section>

  <footer class="contact-bar">
    <span class="contact-web">WWW.GRANITEHOLLOWROOFING.CA</span>
    <span class="contact-phone">403-555-0187</span>
  </footer>

  <svg class="collage" viewBox="480 0 720 457" xmlns="http://www.w3.org/2000/svg">
    <defs>
      <linearGradient id="siding" x1="0" y1="0" x2="1" y2="1">
        <stop offset="0" stop-color="#8d9aa8"/>
        <stop offset="1" stop-color="#b8c1c9"/>
      </linearGradient>
      <linearGradient id="worker" x1="0" y1="0" x2="1" y2="1">
        <stop offset="0" stop-color="#c9d3dc"/>
        <stop offset="0.55" stop-color="#d9733a"/>
        <stop offset="1" stop-color="#4a3a36"/>
      </linearGradient>
      <linearGradient id="garage" x1="0" y1="0" x2="1" y2="1">
        <stop offset="0" stop-color="#b9cfe0"/>
        <stop offset="0.5" stop-color="#6f7e8c"/>
        <stop offset="1" stop-color="#8a7a5a"/>
      </linearGradient>
      <linearGradient id="redhouse" x1="0" y1="0" x2="1" y2="1">
        <stop offset="0" stop-color="#a9b2b9"/>
        <stop offset="0.5" stop-color="#8e8e90"/>
        <stop offset="1" stop-color="#8c2a2c"/>
      </linearGradient>
      <linearGradient id="underlay" x1="0" y1="0" x2="1" y2="1">
        <stop offset="0" stop-color="#6d737a"/>
        <stop offset="1" stop-color="#9aa2a8"/>
      </linearGradient>
      <linearGradient id="driveway" x1="0" y1="0" x2="0" y2="1">
        <stop offset="0" stop-color="#cfe0ee"/>
        <stop offset="0.5" stop-color="#8f9aa3"/>
        <stop offset="1" stop-color="#3b3f44"/>
      </linearGradient>
    </defs>

    <polygon role="img" aria-label="Photo: house siding with scaffolding" fill="url(#siding)"
             points="772,0 1098,0 996,152 766,38"/>
    <polygon role="img" aria-label="Photo: grey roof underlayment" fill="url(#underlay)"
             points="1108,0 1200,0 1200,160 1115,88 1060,70"/>
    <polygon role="img" aria-label="Photo: roofer in hard hat fastening metal roofing panels" fill="url(#worker)"
             points="764,44 992,158 880,370 634,258"/>
    <polygon role="img" aria-label="Photo: grey garage with new shingle roof" fill="url(#garage)"
             points="630,262 876,376 832,457 503,457"/>
    <polygon role="img" aria-label="Photo: red house with grey shingle roof and skylight" fill="url(#redhouse)"
             points="1120,92 1200,135 1200,457 1188,457 1168,420 948,300 1058,110"/>
    <polygon role="img" aria-label="Photo: finished home with company truck and trailer in driveway" fill="url(#driveway)"
             points="942,306 1160,424 1178,457 842,457 890,370"/>
  </svg>

</main>
</body>
</html>
```